Website creation for audiovisual activities

I want a website for my director of photography activity. It's primarily composed of screenshots in gallery format, followed by detailed pages for each production.

Here's my current website:
www.lionelbaquet.com
I'd like a more modern and streamlined design, and for the site to be responsive on phones and computers. I also want to be able to easily add photos and text to it later.

Target Market(s)

productions society, directors and producers.

Industry/Entity Type

Audiovisual / TV

Coding

Coded - Design and coding required

Number of Pages Required

5+ page

Font styles to use
Sans Serif

Colors
0054AA
0677BA
7BADD7
CADEEF
E8F1F8
0094D4
00A9DD
6FCCEA
C7EBF8
E9F6FB
00AB8E
00BBA5
67D7C9
C6EFE9
E9F9F6
6B429C
8869AF
B7A5CE
E3DAEB
F3F0F8

Requirements
Must have
• a modern look with a photo gallery on the homepage
Nice to have
• a light background with large, dynamic images
Should not have
• a dark background and an overly classic look

```html
<!DOCTYPE html>
<html lang="en">
<head>
<meta charset="utf-8">
<title>Mathis Devaure — Director of Photography</title>
<link href="https://fonts.googleapis.com/css2?family=Outfit:wght@200;300;400;500;600&display=swap" rel="stylesheet">
<style>
:root{
  --navy:#1c3392;
  --navy-deep:#16297a;
  --gold:#b9a27f;
  --ink:#1d1d2b;
  --text:#4a4a57;
  --mist:#eef1f8;
  --white:#ffffff;
}
*{margin:0;padding:0;box-sizing:border-box}
html,body{width:1200px;height:4043px;overflow:hidden}
body{position:relative;background:var(--white);font-family:"Outfit",sans-serif;color:var(--ink)}
.abs{position:absolute}
.photo{position:absolute;display:block}

/* header */
.hero-band{left:0;top:0;width:1200px;height:486px;background:linear-gradient(180deg,#1a3190 0%,#1c3392 60%,#1e369a 100%)}
.header-line{left:0;top:78px;width:1200px;height:1px;background:rgba(255,255,255,.08)}
.brand{left:143px;top:12px;color:var(--white)}
.brand-name{font-weight:200;font-size:27px;letter-spacing:.5px;line-height:1}
.brand-tag{font-weight:300;font-size:19px;color:var(--gold);margin-left:34px;letter-spacing:1.5px;line-height:1.2}
.nav{left:447px;top:32px;display:flex;gap:28px;font-size:13px;color:var(--white);letter-spacing:.3px}
.nav a{color:inherit;text-decoration:none;position:relative}
.nav a.active{color:#d9d9e8}
.nav a.active::before{content:"";position:absolute;left:0;right:0;top:-11px;height:2px;background:var(--gold)}
.btn{display:inline-flex;align-items:center;justify-content:center;background:var(--gold);color:var(--ink);font-size:13px;font-weight:500;text-transform:uppercase;text-decoration:none}
.talk{left:949px;top:19px;width:107px;height:37px}
.hero-title{left:0;width:1200px;top:136px;text-align:center;font-size:64px;font-weight:600;color:var(--gold);line-height:1;letter-spacing:1px}
.hero-sub{left:0;width:1200px;top:214px;text-align:center;font-size:39px;font-weight:500;color:var(--white);line-height:1}

/* featured */
.section-title{font-size:41px;font-weight:500;color:var(--ink);line-height:1;text-transform:uppercase}
.fw-title{left:141px;top:926px}
.tab{height:41px;top:927px;font-size:13px;font-weight:600}
.tab.past{left:718px;width:146px}
.tab.current{left:878px;width:178px;background:var(--navy-deep);color:var(--white)}
.card-title{width:436px;text-align:center;font-size:24px;font-weight:400;text-transform:uppercase;line-height:1}
.card-title.hl{color:var(--navy-deep);font-weight:600}
.card-link{width:436px;text-align:center;font-size:15px;font-weight:500;color:var(--gold);text-decoration:underline;text-underline-offset:3px}

/* story */
.story-band{left:0;top:1832px;width:373px;height:636px;background:linear-gradient(160deg,#1d3596 0%,#1c3392 55%,#223a9e 100%)}
.story-bg{left:373px;top:1832px;width:827px;height:636px;background:linear-gradient(135deg,#f1f3f9 0%,#e7ebf6 50%,#eef1f8 100%)}
.gold-bar{background:var(--gold);height:16px}
.body{font-size:14px;line-height:22.5px;color:var(--text);text-align:justify;font-weight:300}
.learn{height:40px;width:146px;font-size:12px;font-weight:600}

/* video */
.video{left:0;top:2468px;width:1200px;height:454px}
.play{left:545px;top:2640px;width:110px;height:110px;border-radius:50%;background:var(--gold)}
.quote-box{left:144px;top:2819px;width:912px;height:256px;background:var(--white)}
.quote{left:220px;top:2876px;width:760px;text-align:center;font-size:32px;font-weight:500;line-height:40px;color:var(--ink)}

/* footer */
.footer{left:0;top:3668px;width:1200px;height:375px;background:linear-gradient(180deg,#1c3392 0%,#1c3392 60%,#1a2f86 100%)}
.f-brand{left:143px;top:3810px;color:var(--white)}
.f-col{top:3762px;color:var(--white)}
.f-col h4{font-size:24px;font-weight:400;text-transform:uppercase;margin-bottom:20px;line-height:1}
.f-col li{list-style:none;font-size:15px;line-height:28px;font-weight:300}
.email{left:789px;top:3817px;width:267px;border-bottom:1px solid rgba(255,255,255,.7);height:28px;font-size:15px;color:#d7dcf0;font-weight:300}
.social{top:3865px;width:34px;height:34px;border-radius:50%;border:1.5px solid var(--white)}
.social.first{background:var(--gold);border-color:var(--gold)}
.copy{left:413px;top:3974px;font-size:14px;color:var(--white);font-weight:300}
</style>
</head>
<body>

<header>
  <div class="abs hero-band"></div>
  <div class="abs header-line"></div>
  <div class="abs brand">
    <div class="brand-name">MATHIS DEVAURE</div>
    <div class="brand-tag">Directeur Photo</div>
  </div>
  <nav class="abs nav">
    <a class="active" href="#">HOME</a><a href="#">ABOUT</a><a href="#">PORTFOLIO</a><a href="#">SPECTACLE</a><a href="#">NEWS</a><a href="#">CONTACT</a>
  </nav>
  <a class="abs btn talk" href="#">Talk info</a>
  <h1 class="abs hero-title">MATHIS DEVAURE</h1>
  <p class="abs hero-sub">DIRECTOR OF PHOTOGRAPHY</p>
  <div class="photo" role="img" aria-label="TV talk show set with three guests seated around a low wooden table" style="left:56px;top:282px;width:1088px;height:545px;background:radial-gradient(ellipse at 50% 85%,rgba(150,100,55,.9) 0%,rgba(150,100,55,0) 45%),radial-gradient(ellipse at 20% 30%,rgba(110,120,60,.8) 0%,rgba(110,120,60,0) 40%),radial-gradient(ellipse at 80% 25%,rgba(215,185,140,.8) 0%,rgba(215,185,140,0) 45%),linear-gradient(135deg,#6e4a2a 0%,#b98a55 40%,#a87a48 65%,#5a3a22 100%)"></div>
</header>

<section class="featured">
  <h2 class="abs section-title fw-title">Featured Work</h2>
  <a class="abs btn tab past" href="#">Past projects</a>
  <a class="abs btn tab current" href="#">Current projects</a>

  <div class="photo" role="img" aria-label="Trailer still: soldier in a dark trench" style="left:143px;top:996px;width:436px;height:254px;background:radial-gradient(ellipse at 55% 40%,rgba(120,125,120,.85) 0%,rgba(120,125,120,0) 45%),linear-gradient(90deg,#141516 0%,#3b3d3e 40%,#4c4e4c 60%,#232220 100%)"></div>
  <p class="abs card-title hl" style="left:143px;top:1273px">Bande Annonce</p>
  <a class="abs card-link" style="left:143px;top:1320px">LEARN MORE</a>

  <div class="photo" role="img" aria-label="Game show studio set with red floor" style="left:620px;top:996px;width:436px;height:254px;background:radial-gradient(ellipse at 45% 95%,rgba(200,40,40,.95) 0%,rgba(200,40,40,0) 40%),radial-gradient(ellipse at 75% 30%,rgba(200,120,70,.8) 0%,rgba(200,120,70,0) 45%),linear-gradient(135deg,#2b2f36 0%,#4f4b4a 50%,#6a3a30 100%)"></div>
  <p class="abs card-title" style="left:620px;top:1273px">Vente Express</p>
  <a class="abs card-link" style="left:620px;top:1320px">LEARN MORE</a>

  <div class="photo" role="img" aria-label="Actor seated on stage in a red theatre" style="left:143px;top:1380px;width:436px;height:253px;background:radial-gradient(ellipse at 65% 60%,rgba(40,40,50,.8) 0%,rgba(40,40,50,0) 30%),radial-gradient(ellipse at 30% 55%,rgba(240,200,170,.6) 0%,rgba(240,200,170,0) 35%),linear-gradient(180deg,#4a1512 0%,#9c2e22 45%,#7a2018 75%,#3a0f0c 100%)"></div>
  <p class="abs card-title" style="left:143px;top:1657px">Soirée Lumière</p>
  <a class="abs card-link" style="left:143px;top:1702px">LEARN MORE</a>

  <div class="photo" role="img" aria-label="Performer in a long red cape on a red padded stage" style="left:620px;top:1380px;width:436px;height:253px;background:radial-gradient(ellipse at 50% 60%,#f5a05a 0%,#e0502a 30%,#b02a18 60%,#1a0806 100%)"></div>
  <p class="abs card-title" style="left:620px;top:1657px">Élias Moreau</p>
  <a class="abs card-link" style="left:620px;top:1702px">LEARN MORE</a>
</section>

<section class="story">
  <div class="abs story-band"></div>
  <div class="abs story-bg"></div>
  <div class="photo" role="img" aria-label="Pianist playing a grand piano in a gilded palace hall" style="left:141px;top:1975px;width:439px;height:378px;background:radial-gradient(ellipse at 75% 55%,rgba(20,18,16,.9) 0%,rgba(20,18,16,0) 30%),radial-gradient(ellipse at 30% 25%,rgba(230,200,130,.9) 0%,rgba(230,200,130,0) 45%),linear-gradient(180deg,#c9a45e 0%,#a57a42 50%,#6a4a2a 100%)"></div>
  <div class="abs gold-bar" style="left:322px;top:2353px;width:219px"></div>
  <h2 class="abs section-title" style="left:629px;top:1985px">Our Story</h2>
  <p class="abs body" style="left:629px;top:2032px;width:427px">Lorem ipsum dolor sit amet, consectetur adipiscing elit, sed do eiusmod tempor incididunt ut labore et dolore magna aliqua. Ut enim ad minim veniam, quis nostrud exercitation ullamco laboris nisi ut aliquip ex ea commodo consequat. Duis aute irure dolor in reprehenderit in voluptate velit esse cillum dolore eu fugiat nulla pariatur. Excepteur sint occaecat cupidatat non proident, sunt in culpa qui officia deserunt mollit anim id est laborum. Lorem ipsum dolor sit amet, consectetur adipiscing elit, sed do eiusmod tempor incididunt ut labore et dolore magna aliqua. Ut enim ad minim veniam, quis nostrud exercitation ullamco laboris nisi ut aliquip ex ea commodo consequat.</p>
  <a class="abs btn learn" href="#" style="left:629px;top:2293px">Learn more</a>
</section>

<section class="showreel">
  <div class="photo video" role="img" aria-label="Concert stage with blue spotlights and falling golden confetti" style="background:radial-gradient(ellipse at 15% 50%,rgba(70,120,230,.7) 0%,rgba(70,120,230,0) 30%),radial-gradient(ellipse at 85% 55%,rgba(70,120,230,.6) 0%,rgba(70,120,230,0) 30%),radial-gradient(ellipse at 50% 20%,rgba(190,140,70,.45) 0%,rgba(190,140,70,0) 50%),radial-gradient(ellipse at 90% 90%,rgba(180,70,40,.5) 0%,rgba(180,70,40,0) 30%),linear-gradient(180deg,#0c1138 0%,#1a2370 55%,#0e1440 100%)"></div>
  <div class="abs play"></div>
  <svg class="abs" style="left:545px;top:2640px" width="110" height="110" viewBox="0 0 110 110" aria-hidden="true"><path d="M47 42 L68 55 L47 68 Z" fill="#fff"/></svg>
  <div class="abs quote-box"></div>
  <p class="abs quote">Entertainment magazines, news programs, political debates, game shows, concert recordings, music videos, short fiction films, documentaries, commercials, and corporate films</p>
</section>

<section class="about">
  <h2 class="abs section-title" style="left:141px;top:3190px">About Me</h2>
  <p class="abs body" style="left:141px;top:3240px;width:428px">Lorem ipsum dolor sit amet, consectetur adipiscing elit, sed do eiusmod tempor incididunt ut labore et dolore magna aliqua. Ut enim ad minim veniam, quis nostrud exercitation ullamco laboris nisi ut aliquip ex ea commodo consequat. Duis aute irure dolor in reprehenderit in voluptate velit esse cillum dolore eu fugiat nulla pariatur. Excepteur sint occaecat cupidatat non proident, sunt in culpa qui officia deserunt mollit anim id est laborum. Lorem ipsum dolor sit amet, consectetur adipiscing elit, sed do eiusmod tempor incididunt ut labore et dolore magna aliqua. Ut enim ad minim veniam, quis nostrud exercitation ullamco laboris nisi ut aliquip ex ea commodo consequat.</p>
  <a class="abs btn learn" href="#" style="left:141px;top:3511px">Learn more</a>
  <div class="photo" role="img" aria-label="Interview in a stone hall with statues and a tall window" style="left:616px;top:3175px;width:440px;height:378px;background:radial-gradient(ellipse at 55% 28%,rgba(200,205,215,.75) 0%,rgba(200,205,215,0) 25%),radial-gradient(ellipse at 12% 40%,rgba(190,170,140,.8) 0%,rgba(190,170,140,0) 30%),linear-gradient(180deg,#7a6a56 0%,#564a3e 50%,#1c2040 100%)"></div>
  <div class="abs gold-bar" style="left:656px;top:3553px;width:218px"></div>
</section>

<footer>
  <div class="abs footer"></div>
  <div class="abs brand f-brand">
    <div class="brand-name">MATHIS DEVAURE</div>
    <div class="brand-tag">Directeur Photo</div>
  </div>
  <div class="abs f-col" style="left:413px"><h4>About us</h4><ul><li>About US</li><li>Contact</li><li>Faq</li><li>Our Company</li></ul></div>
  <div class="abs f-col" style="left:596px"><h4>More info</h4><ul><li>Career</li><li>Team</li><li>Services</li><li>Portfolio</li></ul></div>
  <div class="abs f-col" style="left:789px"><h4>Newsletter</h4></div>
  <div class="abs email">Email</div>
  <svg class="abs" style="left:1028px;top:3818px" width="18" height="18" viewBox="0 0 18 18" aria-hidden="true"><path d="M2 9 L16 2 L12 16 L9 10 Z" fill="#b9a27f"/></svg>
  <span class="abs social first" style="left:789px"></span>
  <span class="abs social" style="left:836px"></span>
  <span class="abs social" style="left:885px"></span>
  <p class="abs copy">Copyright © 2026 Mathis Devaure. All rights reserved.</p>
</footer>

</body>
</html>
```